BOLD & MINIMALIST DESIGN NEEDED

We want a very bold but minimalistic business card design that is impactful and utilizes both sides of the business card. Our current logo is included for your use.

We want bold fonts and good use of negative space. We don't want the logo to overpower the design.

Target Market(s)

Professionals who are building new commercial buildings.

Industry/Entity Type

Construction

Contact Information for Business Card

Name, Title, email, office phone, cell phone, website

Font styles to use
Serif
Sans Serif

Requirements
Must have
• Bold design!

```html
<!DOCTYPE html>
<html lang="en">
<head>
<meta charset="utf-8">
<title>Ridgeline Design + Build — Business Card</title>
<link href="https://fonts.googleapis.com/css2?family=Montserrat:wght@400;700;800&display=swap" rel="stylesheet">
<style>
  :root {
    --backdrop: #dcdcdc;
    --paper: #ffffff;
    --ink: #0d0e10;
    --accent: #8fcb58;
    --muted: #6b6b6b;
  }
  * { margin: 0; padding: 0; box-sizing: border-box; }
  html, body { width: 1200px; height: 1200px; overflow: hidden; }
  body {
    background: var(--backdrop);
    position: relative;
    font-family: "Montserrat", sans-serif;
  }
  .card {
    position: absolute;
    left: 180px;
    width: 867px;
    height: 499px;
    overflow: hidden;
  }
  .card--front { top: 85px; background: var(--paper); }
  .card--back { top: 625px; background: var(--ink); }

  .wordmark {
    position: absolute;
    text-align: center;
    color: var(--ink);
    font-weight: 800;
    line-height: 1;
  }
  .wordmark__name { display: block; letter-spacing: 0.02em; }
  .wordmark__tag { display: block; letter-spacing: 0.32em; }

  .card--front .wordmark {
    left: 0; right: 0; top: 205px;
  }
  .card--front .wordmark__name { font-size: 64px; }
  .card--front .wordmark__tag { font-size: 20px; margin-top: 12px; padding-left: 0.32em; }

  .back-shapes { position: absolute; inset: 0; width: 100%; height: 100%; }

  .card--back .wordmark {
    left: 32px; width: 300px; top: 230px;
  }
  .card--back .wordmark__name { font-size: 46px; }
  .card--back .wordmark__tag { font-size: 15px; margin-top: 9px; padding-left: 0.32em; }

  .person {
    position: absolute;
    right: 40px;
    top: 120px;
    text-align: right;
  }
  .person__name {
    color: var(--paper);
    font-weight: 700;
    font-size: 32px;
    line-height: 1.1;
  }
  .person__title {
    color: var(--accent);
    font-weight: 400;
    font-size: 27px;
    letter-spacing: 0.03em;
    line-height: 1.2;
  }

  .contact {
    position: absolute;
    list-style: none;
    color: var(--muted);
    font-size: 24px;
    letter-spacing: 0.04em;
  }
  .contact li {
    display: flex;
    align-items: center;
    height: 35px;
  }
  .contact svg { width: 26px; height: 26px; margin-right: 11px; flex: none; }
  .contact--phones { left: 32px; top: 413px; }
  .contact--online { left: 444px; top: 412px; }
  .contact .highlight { color: var(--accent); }
</style>
</head>
<body>

  <section class="card card--front" aria-label="Card front">
    <div class="wordmark">
      <span class="wordmark__name">RIDGELINE</span>
      <span class="wordmark__tag">DESIGN + BUILD</span>
    </div>
  </section>

  <section class="card card--back" aria-label="Card back">
    <svg class="back-shapes" viewBox="0 0 1387 797" preserveAspectRatio="none" aria-hidden="true">
      <polygon points="0,290 295,160 1387,712 1387,797 0,797" fill="#ffffff"/>
      <polygon points="0,283 295,115 1267,656 295,160" fill="#8fcb58"/>
    </svg>

    <div class="wordmark">
      <span class="wordmark__name">RIDGELINE</span>
      <span class="wordmark__tag">DESIGN + BUILD</span>
    </div>

    <div class="person">
      <p class="person__name">Name Surename</p>
      <p class="person__title">Director</p>
    </div>

    <ul class="contact contact--phones">
      <li>
        <svg viewBox="0 0 24 24" aria-hidden="true"><path fill="#0d0e10" d="M6.6 10.8a15.1 15.1 0 0 0 6.6 6.6l2.2-2.2a1 1 0 0 1 1-.25 11.4 11.4 0 0 0 3.6.57 1 1 0 0 1 1 1V20a1 1 0 0 1-1 1A17 17 0 0 1 3 4a1 1 0 0 1 1-1h3.5a1 1 0 0 1 1 1c0 1.25.2 2.45.57 3.57a1 1 0 0 1-.25 1z"/></svg>
        <span>555-014-2200</span>
      </li>
      <li>
        <svg viewBox="0 0 24 24" aria-hidden="true"><path fill="#0d0e10" d="M2 8c0-2 4-4 10-4s10 2 10 4v2h-5V8.5c-1.5-.6-3.2-.8-5-.8s-3.5.2-5 .8V10H2zM6 11h12l3 6v3H3v-3zm6 2a2.5 2.5 0 1 0 0 5 2.5 2.5 0 0 0 0-5z"/></svg>
        <span>555-014-2200</span>
      </li>
    </ul>

    <ul class="contact contact--online">
      <li>
        <svg viewBox="0 0 24 24" aria-hidden="true"><rect x="2" y="5" width="20" height="14" fill="#0d0e10"/><path d="M3 6l9 7 9-7M3 18l7-6M21 18l-7-6" stroke="#ffffff" stroke-width="1.4" fill="none"/></svg>
        <span>info@r-d-b.com</span>
      </li>
      <li>
        <svg viewBox="0 0 24 24" aria-hidden="true"><g fill="none" stroke="#0d0e10" stroke-width="1.6"><circle cx="12" cy="12" r="10"/><ellipse cx="12" cy="12" rx="4.5" ry="10"/><path d="M2 12h20M4 7h16M4 17h16M12 2v20"/></g></svg>
        <span>www.<span class="highlight">r-d-b</span>.com</span>
      </li>
    </ul>
  </section>

</body>
</html>
```